Corvel Capital LLC

Need Professional Business cards for New Investment Fund

Target Market(s)

High Quality investors

Industry/Entity Type

Financial

Contact Information for Business Card

Phone Number +1 555 284 6190
Name Lukas Varenko
Title Fund Manager
email lv@FundCorvel.com
Website www.FundCorvel.com

Colors

Designer to choose colors to be used in the design.

Requirements
Must have
• Must have our Logo and all of the above. Must be made so lettering and loge can be raised

```html
<!DOCTYPE html>
<html lang="en">
<head>
<meta charset="utf-8">
<title>Business Card – Fund Manager</title>
<link rel="stylesheet" href="https://fonts.googleapis.com/css2?family=Jost:wght@500&family=Roboto:wght@400;500&display=swap">
<style>
  :root {
    --backdrop: #bebebe;
    --card-dark: #3a4540;
    --card-light: #f1f1f1;
    --ink-dark: #3a4540;
    --ink-soft: #4a524e;
    --ink-light: #c9cccb;
    --accent: #8dc63f;
  }
  * { margin: 0; padding: 0; box-sizing: border-box; }
  html, body {
    width: 1200px;
    height: 1138px;
    overflow: hidden;
    background: var(--backdrop);
  }
  .stage { position: relative; width: 1200px; height: 1138px; }
  .card {
    position: absolute;
    border-radius: 16px;
    box-shadow: 0 4px 10px rgba(0,0,0,0.18);
  }
  .card--front {
    left: 274px; top: 186px; width: 622px; height: 376px;
    background: var(--card-dark);
  }
  .card--back {
    left: 276px; top: 608px; width: 618px; height: 374px;
    background: var(--card-light);
  }
  .wordmark {
    position: absolute;
    font-family: "Jost", sans-serif;
    font-weight: 500;
    letter-spacing: 1px;
    line-height: 1;
    white-space: nowrap;
  }
  .card--front .wordmark {
    left: 0; right: 0; top: 160px;
    text-align: center;
    font-size: 72px;
    color: var(--ink-light);
  }
  .card--back .wordmark {
    left: 60px; top: 180px;
    font-size: 50px;
    color: var(--ink-dark);
  }
  .holder {
    position: absolute;
    left: 346px; top: 111px;
    font-family: "Roboto", sans-serif;
    color: var(--ink-dark);
  }
  .holder__name { font-size: 24px; font-weight: 500; line-height: 30px; }
  .holder__title { font-size: 16.5px; color: var(--ink-soft); margin-top: 4px; }
  .contacts {
    position: absolute;
    left: 346px; top: 192px;
    list-style: none;
    font-family: "Roboto", sans-serif;
    font-size: 16.5px;
    color: var(--ink-dark);
  }
  .contacts li {
    display: flex; align-items: center;
    height: 24px;
  }
  .contacts svg { width: 13px; height: 13px; margin-right: 18px; flex: none; }
</style>
</head>
<body>
<main class="stage">
  <section class="card card--front" aria-label="Card front">
    <div class="wordmark">ORLINDE</div>
  </section>

  <section class="card card--back" aria-label="Card back">
    <div class="wordmark">ORLINDE</div>
    <div class="holder">
      <p class="holder__name">Lukas Varenko</p>
      <p class="holder__title">Fund Manager</p>
    </div>
    <ul class="contacts">
      <li>
        <svg viewBox="0 0 14 14" aria-hidden="true"><path fill="var(--accent)" d="M1 5c0-2 2.5-3 6-3s6 1 6 3v1.2h-3V4.8H4v1.4H1zM3.5 7h7l1.5 5.5H2z"/></svg>
        +1 555 284 6190
      </li>
      <li>
        <svg viewBox="0 0 14 14" aria-hidden="true"><rect x="1" y="3" width="12" height="8.5" fill="var(--accent)"/><path d="M1 3l6 5 6-5" fill="none" stroke="#fff" stroke-width="1.1"/></svg>
        lv@FundCorvel.com
      </li>
      <li>
        <svg viewBox="0 0 14 14" aria-hidden="true"><circle cx="7" cy="7" r="6" fill="var(--accent)"/><path d="M1 7h12M7 1c-2.5 3-2.5 9 0 12M7 1c2.5 3 2.5 9 0 12" fill="none" stroke="#fff" stroke-width="0.9"/></svg>
        www.FundCorvel.com
      </li>
    </ul>
  </section>
</main>
</body>
</html>
```